Bold, Modern, Clean "Kestrelwaymassage.com" website

Why we stand out?
We are a male and female mobile massage team. Our names are Paul and Lina. 
Kestrel Way is a Seattle based mobile massage service. Our massage is offered to the community with a goal of facilitating balance within each individual. We specialize in integrated Pain management, and sports/medical massage therapy. Every client's first assessment is attended by our male and female massage therapist team. Depending on the goals identified for an individual determines which therapist will be assigned to provide treatment, if not both.

Our passion...
Here at Kestrel Way, we have a great passion for Postural Resoration and how it is integrated into an individual's Massage treatment. We pride ourselves in being natural facilitators of healing, which takes the ego of the therapist out of the client's healing process. We strive to deliver the best massage possible by including modalities such as Neuromuscular, Myofascial release, spontaneous muscle release, postural restoration, orthopedic, and medical massage.

Our education...

We are both Graduates of Venmora, school of massage therapy. We have continuing education in medical massage, myofacial release, trigger point therapy, postural restoration, anatomy, and spontaneous muscle release. Lina is also a Certified Yoga Instructor, which amplifies her experience with flexibility and strength as it pertains to each individual. Paul's passion is Massage, stretching, and strength training to encourage postural restoration and realignment.

Our rates-

Our rates are $75/ 60 minutes, $95/ 90 minutes, and $120/ 120 minutes.

Education-
Both Lina and I worked as behavioral health professionals that specialized in life skills mentoring for youth who had experienced different types of trauma. This led us both to want to help others in a different environment, where individuals can be empowered to take responsibility over their own healing. To us, massage is a type of manipulation physical therapy, that encourages healing on many levels.

Advice to any massage client-
The most important thing to 'us', as Licenced providers is to get you on to our table to show you our skills. But a good therapist never forgets that it's not about what we do for you, but what we can facilitate for you. Your health and healing has nothing to do with us. It is yours, not ours. Identify what your goals are with any Therapist, and know what the end looks like. Progress should be tangible, such as range of motion, and decreased pain.

Lina and Paul at Kestrel Way are awesome! I recently had open heart surgery, and Lina worked on me to increase my range of motion while helping with the pinched nerve from my arm being in the same position for so long during my surgery. My wife drives a lot for work, and Paul has helped decrease her neck and lower back pain immensely. They are seriously the best therapists I have ever worked with. I would recommend them to anyone who needs anything from stress relief to a medical massage treatment. They are professional, up beat, easy going, and always on time. And, I love that they meet us where ever we like! We did a staycation recently, where they came to our hotel to give us relaxation massages. Although usually they come to our home, where we focus on pain related issues. We will continue to work with them for a long, long time.

Target Market(s)

Mobile massage therapy clients

Industry/Entity Type

Massage Therapy

Coding

Coded - Design and coding required

Number of Pages Required

1 page

Font styles to use
Serif
Sans Serif

Requirements
Must have
• Please add or remove any information that would help the presentation of our website. Our logo is posted below, please include into the website.
• Please include a contact field that includes, kestrelwaymassage@fernmail.net,
• (206) 555-0148
• We have also included our own stock photos, as well as a photo of Paul and Lina. Please include a cropped photo of both massage therapists.

```html
<!DOCTYPE html>
<html lang="en">
<head>
<meta charset="utf-8">
<title>Kestrel Way Mobile Massage</title>
<link href="https://fonts.googleapis.com/css2?family=Open+Sans:ital,wght@0,400;0,600;0,700;1,400&display=swap" rel="stylesheet">
<style>
:root{
  --navy:#1f2d6e;
  --navy-deep:#18245c;
  --blue:#1f4fa0;
  --cyan:#13a9c9;
  --cyan-light:#1bb6d3;
  --teal-btn:#1895b0;
  --text:#333;
  --muted:#666;
  --panel:#f2f2f2;
  --white:#fff;
  --star:#f5c518;
}
*{box-sizing:border-box;margin:0;padding:0}
html,body{width:1200px;height:2203px;overflow:hidden}
body{position:relative;background:var(--white);font-family:"Open Sans",Arial,sans-serif;color:var(--text)}
.abs{position:absolute}

/* header */
.follow{left:98px;top:48px;display:flex;align-items:center;gap:10px;font-size:13px;color:#333;z-index:2}
.follow .dot{width:34px;height:34px;border-radius:50%;background:#f3f3f3;display:inline-block}
.quick-call{right:98px;top:42px;display:flex;align-items:center;gap:12px;font-size:13px;color:#333;z-index:2}
.quick-call .ring{width:42px;height:42px;border-radius:50%;border:2px solid var(--navy);display:flex;align-items:center;justify-content:center}
.quick-call b{font-weight:400;color:var(--navy)}

.nav{left:98px;top:128px;width:1003px;height:56px;background:linear-gradient(90deg,var(--navy),#243a86 50%,var(--navy));font-size:13px;color:#fff;border-radius:0 3px 3px 0;z-index:2;box-shadow:0 2px 4px rgba(0,0,0,.15)}
.nav a{color:#fff;text-decoration:none;position:absolute;top:0;height:56px;line-height:56px}
.nav .home{left:0;width:90px;background:var(--cyan);text-align:center}

.brand{left:530px;top:25px;width:140px;height:140px;border-radius:50%;background:var(--white);box-shadow:0 2px 6px rgba(0,0,0,.2);display:flex;align-items:center;justify-content:center;z-index:3}
.brand .disc{width:124px;height:124px;border-radius:50%;background:var(--blue);border:3px solid var(--navy);display:flex;flex-direction:column;align-items:center;justify-content:center;color:#fff;font-weight:700;font-size:21px;line-height:1.05;text-align:center}

/* hero */
.hero{left:0;top:156px;width:1200px;height:545px;background:linear-gradient(120deg,#cfc7bd 0%,#e9e4dd 45%,#f4f1ec 70%,#ddd6cc 100%);z-index:0}
.hero-title{left:96px;top:382px;font-size:58px;font-weight:700;color:#fff;text-shadow:0 2px 4px rgba(0,0,0,.3);z-index:1}
.hero-sub{left:96px;top:452px;font-size:29px;color:#fff;text-shadow:0 1px 3px rgba(0,0,0,.3);z-index:1}
.dots{left:98px;top:504px;display:flex;gap:8px;z-index:1}
.dots i{width:12px;height:12px;border-radius:50%;background:#eee;display:block}
.dots i.on{background:var(--cyan)}

.contact-card{left:846px;top:286px;width:254px;height:310px;background:#fff;box-shadow:0 2px 8px rgba(0,0,0,.25);border-radius:3px;z-index:1}
.contact-card .head{height:58px;background:var(--blue);color:#fff;font-size:14px;text-align:center;padding-top:16px;clip-path:polygon(0 0,100% 0,100% 70%,50% 100%,0 70%)}
.field{position:absolute;left:14px;width:226px;border:1px solid #ddd;font-size:10px;color:#777;padding:9px 10px}
.btn{position:absolute;left:14px;top:248px;width:226px;height:40px;background:linear-gradient(var(--cyan-light),var(--teal-btn));color:#fff;font-size:13px;text-align:center;line-height:40px;border-radius:2px}

/* welcome */
.welcome-title{left:0;top:736px;width:1200px;text-align:center;font-size:26px;font-weight:400;color:#333}
.welcome-copy{left:135px;top:782px;width:930px;text-align:center;font-size:11.5px;font-style:italic;color:#555;line-height:24px}

.service{top:921px;width:310px;height:264px;background:var(--panel);text-align:center;box-shadow:0 8px 10px -8px rgba(0,0,0,.25)}
.service .icon{width:122px;height:122px;border-radius:50%;border:3px solid var(--navy);margin:24px auto 0;display:flex;align-items:center;justify-content:center}
.service .icon span{width:110px;height:110px;border-radius:50%;background:var(--navy);display:flex;align-items:center;justify-content:center}
.service h3{font-weight:400;font-size:14.5px;color:var(--navy);margin-top:18px}
.service p{font-size:10.5px;color:#666;line-height:20px;margin:6px 24px 0}

/* advice band */
.band{left:0;top:1252px;width:1200px;height:402px;background:linear-gradient(135deg,var(--cyan-light),var(--cyan) 50%,#11a0bf)}
.advice{left:98px;top:1309px;width:695px;height:279px;background:linear-gradient(90deg,#fff 40%,#eef0ef)}
.advice h2{position:absolute;left:52px;top:40px;font-weight:400;font-size:21px;color:#333}
.advice p{position:absolute;left:52px;width:580px;font-size:11px;font-style:italic;color:#666;line-height:26px}
.reviews{left:793px;top:1309px;width:307px;height:279px;background:var(--navy)}
.review{height:69.75px;border-bottom:1px solid #2e3d80;display:flex;align-items:center;padding-left:12px;gap:14px;color:#fff;font-size:12px}
.review:last-child{border-bottom:none}
.avatar{width:48px;height:48px;background:linear-gradient(#c9b8a8,#8d7565);border:2px solid #fff}
.stars{color:var(--star);font-size:12px;margin-top:2px}

/* rates */
.rates{left:209px;top:1714px;width:891px;height:328px;background:#f3f4f6}
.rates h2{position:absolute;left:0;top:36px;width:100%;text-align:center;font-weight:400;font-size:21px;color:var(--navy)}
.rates p{position:absolute;left:50px;top:84px;width:790px;text-align:center;font-size:11.5px;font-style:italic;color:#555;line-height:25px}
.person{left:98px;top:1719px;width:111px;height:301px;background:linear-gradient(#e8d6c6 0%,#d9b89c 35%,#2f4ab8 55%,#2a3fa3 100%);border-radius:40px 0 0 0}
.price{width:122px;height:122px;border-radius:50%;border:3px solid var(--navy);display:flex;align-items:center;justify-content:center}
.price div{width:110px;height:110px;border-radius:50%;background:var(--navy);color:#fff;text-align:center;padding-top:26px}
.price b{display:block;font-size:26px;font-weight:700}
.price span{font-size:13px}

/* footer */
.footer{left:0;top:2098px;width:1200px;height:105px;background:linear-gradient(90deg,var(--navy-deep),var(--blue) 50%,var(--navy-deep));color:#fff;font-size:12px}
.footer .mark{position:absolute;left:98px;top:10px;width:86px;height:86px;border-radius:50%;background:#fff;display:flex;align-items:center;justify-content:center}
.footer .mark span{width:76px;height:76px;border-radius:50%;background:var(--blue);color:#fff;font-weight:700;font-size:13px;display:flex;align-items:center;justify-content:center;text-align:center;line-height:1.1}
.footer .links{position:absolute;left:196px;top:44px}
.footer .copy{position:absolute;right:98px;top:44px}
</style>
</head>
<body>

<div class="abs hero" role="img" aria-label="Therapist giving a leg stretch massage to a client on a treatment table"></div>

<header>
  <div class="abs follow">Follow With Us:
    <span class="dot"></span><span class="dot"></span><span class="dot"></span><span class="dot"></span>
  </div>
  <div class="abs brand"><div class="disc">KESTREL<br>WAY</div></div>
  <div class="abs quick-call">
    <span class="ring"><svg width="18" height="18" viewBox="0 0 24 24"><path fill="#1f2d6e" d="M6.6 10.8c1.4 2.8 3.8 5.1 6.6 6.6l2.2-2.2c.3-.3.7-.4 1-.2 1.1.4 2.3.6 3.6.6.6 0 1 .4 1 1V20c0 .6-.4 1-1 1C10.6 21 3 13.4 3 4c0-.6.4-1 1-1h3.5c.6 0 1 .4 1 1 0 1.3.2 2.5.6 3.6.1.3 0 .7-.2 1z"/></svg></span>
    <span>Quick Contact - <b>(206) 555-0148</b></span>
  </div>
  <nav class="abs nav">
    <a class="home" href="#">Home</a>
    <a href="#" style="left:157px">About</a>
    <a href="#" style="left:285px">Services</a>
    <a href="#" style="left:655px">Massage</a>
    <a href="#" style="left:797px">Gallery</a>
    <a href="#" style="left:928px">Contact</a>
  </nav>
</header>

<section>
  <div class="abs hero-title">Seattle Based</div>
  <div class="abs hero-sub">Mobile Massage</div>
  <div class="abs dots"><i></i><i></i><i class="on"></i></div>

  <form class="abs contact-card">
    <div class="head">Quick Contact</div>
    <div class="field" style="top:76px">Name*</div>
    <div class="field" style="top:119px">E-mail*</div>
    <div class="field" style="top:162px;height:76px">Message*</div>
    <div class="btn">Subscribe Here</div>
  </form>
</section>

<section>
  <h1 class="abs welcome-title">Welcome to Kestrel Way Massage</h1>
  <p class="abs welcome-copy">We are a male and female mobile massage team. Our names are Paul and Lina. Kestrel Way is a Seattle based mobile massage service. Our massage is offered to the community with a goal of facilitating balance within each individual. We specialize in integrated Pain management, and sports/medical massage therapy. Every client's first assessment is attended by our male and female massage therapist team. Depending on the goals identified for an individual determines which therapist will be assigned to provide treatment, if not both.</p>

  <div class="abs service" style="left:98px">
    <div class="icon"><span><svg width="56" height="56" viewBox="0 0 56 56" fill="#fff"><circle cx="30" cy="12" r="6"/><path d="M22 20h14l4 12H26zM6 36h44v5H6zM8 41h4v6H8zM44 41h4v6h-4z"/><ellipse cx="14" cy="32" rx="6" ry="3.5"/></svg></span></div>
    <h3>Pain Management Massage</h3>
    <p>Sed ut perspiciatis unde omnis iste natus error sit, totam rem aperiam, eaque ipsa quae consequunt ur magni dolores eos qui ration...</p>
  </div>
  <div class="abs service" style="left:445px">
    <div class="icon"><span><svg width="56" height="56" viewBox="0 0 56 56" fill="#fff"><path d="M30 6c5 8 9 13 9 18a9 9 0 0 1-18 0c0-5 4-10 9-18z"/><path d="M6 38h10l10 4h12c2 0 2 4 0 4H26v1h14l10-7c2-1 4 1 2 3L40 52H6z"/></svg></span></div>
    <h3>Sports Massage Therapy</h3>
    <p>Sed ut perspiciatis unde omnis iste natus error sit, totam rem aperiam, eaque ipsa quae consequunt ur magni dolores eos qui ration...</p>
  </div>
  <div class="abs service" style="left:790px">
    <div class="icon"><span><svg width="60" height="56" viewBox="0 0 60 56"><path fill="#fff" d="M30 50C10 36 4 27 4 18 4 10 10 5 17 5c6 0 10 4 13 8 3-4 7-8 13-8 7 0 13 5 13 13 0 9-6 18-26 32z"/><path fill="none" stroke="#1f2d6e" stroke-width="3" stroke-linejoin="round" d="M10 26h10l4-8 6 16 5-12 3 4h12"/></svg></span></div>
    <h3>Medical Massage Therapy</h3>
    <p>Sed ut perspiciatis unde omnis iste natus error sit, totam rem aperiam, eaque ipsa quae consequunt ur magni dolores eos qui ration...</p>
  </div>
</section>

<section>
  <div class="abs band"></div>
  <div class="abs advice" role="img" aria-label="Faded background photo of a client relaxing during a massage">
    <h2>Advice to any Massage Client</h2>
    <p style="top:80px">The most important thing to 'us', as Licenced providers is to get you on to our table to show you our skills. But a good therapist never forgets that it's not about what we do for you, but what we can facilitate for you. Your health and healing has nothing to do with us.</p>
    <p style="top:178px">It is yours, not ours. Identify what your goals are with any Therapist, and know what the end looks like. Progress should be tangible, such as range of motion, and decreased pain...</p>
  </div>
  <div class="abs reviews">
    <div class="review"><div class="avatar" role="img" aria-label="Client portrait"></div><div>Accusantium doloremque laudantim...<div class="stars">★★★★★</div></div></div>
    <div class="review"><div class="avatar" role="img" aria-label="Client portrait"></div><div>Accusantium doloremque laudantim...<div class="stars">★★★★★</div></div></div>
    <div class="review"><div class="avatar" role="img" aria-label="Client portrait"></div><div>Accusantium doloremque laudantim...<div class="stars">★★★★★</div></div></div>
    <div class="review"><div class="avatar" role="img" aria-label="Client portrait"></div><div>Accusantium doloremque laudantim...<div class="stars">★★★★★</div></div></div>
  </div>
</section>

<section>
  <div class="abs rates">
    <h2>Our Rates</h2>
    <p>Both Lina and I worked as behavioral health professionals that specialized in life skills mentoring for youth who had experienced different types of trauma. This led us both to want to help others in a different environment, where individuals can be empowered to...</p>
  </div>
  <div class="abs person" role="img" aria-label="Smiling woman in a blue top peeking from behind the rates panel"></div>
  <div class="abs price" style="left:312px;top:1860px"><div><b>$75</b><span>60 minutes</span></div></div>
  <div class="abs price" style="left:594px;top:1860px"><div><b>$95</b><span>90 minutes</span></div></div>
  <div class="abs price" style="left:876px;top:1860px"><div><b>$120</b><span>120 minutes</span></div></div>
  <svg class="abs" style="left:440px;top:1880px" width="150" height="90" viewBox="0 0 150 90"><path d="M6 50C40 10 90 10 120 48" fill="none" stroke="#c8c8c8" stroke-width="12" stroke-linecap="round"/><path d="M104 40l32 22-6-38z" fill="#c8c8c8"/></svg>
  <svg class="abs" style="left:722px;top:1880px" width="150" height="90" viewBox="0 0 150 90"><path d="M8 40c30 40 80 40 112 6" fill="none" stroke="#c8c8c8" stroke-width="12" stroke-linecap="round"/><path d="M108 30l36-16-8 38z" fill="#c8c8c8"/></svg>
</section>

<footer class="abs footer">
  <div class="mark"><span>KESTREL<br>WAY</span></div>
  <div class="links">Home &nbsp;\&nbsp; About &nbsp;\&nbsp; Servic Massage &nbsp;\&nbsp; Gallery &nbsp;\&nbsp; Contact</div>
  <div class="copy">Copyrights © kestrelwaymassage . 2015 | Allrights Reserved.</div>
</footer>

</body>
</html>
```